business card for a massage therapy practice named 'Cedar and Willow Massage Studio'

I really need a trendy, yet easy on the eyes business card to complement my logo. Ideally with some gold or rose gold foil work.

My uploaded file of the logo I have in horizontal but I have a vertical version as well. Another color that is used in the website is a blush pink here and there. I'd like to see some trendy tropical leaves in the design.

```html
<!DOCTYPE html>
<html lang="en">
<head>
<meta charset="utf-8">
<title>Cedar and Willow Massage Studio — Business Card</title>
<link rel="stylesheet" href="https://fonts.googleapis.com/css2?family=Pinyon+Script&family=Tinos:wght@400;700&display=swap">
<style>
  :root {
    --backdrop: #ecebe8;
    --paper: #f8f7f4;
    --foil: #b8885c;
    --leaf-light: #a6e3d2;
    --leaf: #74d1b7;
    --card-shadow: rgba(0, 0, 0, 0.12);
  }
  html, body {
    margin: 0;
    padding: 0;
    overflow: hidden;
  }
  .canvas {
    position: relative;
    width: 966px;
    height: 1200px;
    background: var(--backdrop);
    overflow: hidden;
  }
  .card {
    position: absolute;
    left: 183px;
    width: 600px;
    height: 350px;
    background: var(--paper);
    box-shadow: 0 6px 18px var(--card-shadow);
    overflow: hidden;
    color: var(--foil);
    font-family: "Tinos", "Times New Roman", serif;
  }
  .card--front { top: 130px; }
  .card--back { top: 720px; }

  .contact {
    position: absolute;
    left: 40px;
    top: 38px;
    font-weight: 700;
  }
  .contact__name {
    font-family: "Pinyon Script", cursive;
    font-weight: 400;
    font-size: 30px;
    line-height: 1;
    margin: 0;
  }
  .contact__role {
    font-size: 16px;
    margin: 2px 0 26px;
  }
  .contact__block {
    font-size: 13.5px;
    line-height: 1.45;
    margin: 0 0 12px;
  }

  .palm-fronds {
    position: absolute;
    right: 0;
    bottom: 0;
    width: 330px;
    height: 290px;
  }

  .brand {
    position: absolute;
    left: 0;
    right: 0;
    top: 118px;
    display: flex;
    align-items: center;
    justify-content: center;
    gap: 22px;
  }
  .brand__dot {
    width: 34px;
    height: 34px;
    border-radius: 50%;
    background: var(--foil);
  }
  .brand__name {
    font-size: 38px;
    line-height: 1.1;
    font-weight: 400;
    margin: 0;
  }
  .brand__tagline {
    font-size: 20px;
    letter-spacing: 5px;
    text-transform: uppercase;
    margin: 4px 0 0;
    font-weight: 400;
  }
</style>
</head>
<body>
<main class="canvas">

  <section class="card card--front" aria-label="Business card front">
    <div class="contact">
      <h1 class="contact__name">Marisol Reyes</h1>
      <p class="contact__role">Massage Therapist</p>
      <p class="contact__block">2140 Alder Ave #210<br>Riverton, CA 95031</p>
      <p class="contact__block">P. (555) 214-7380<br>info@cedarandwillow.com<br>www.cedarandwillow.com</p>
    </div>
    <svg class="palm-fronds" viewBox="0 0 330 290" role="img" aria-label="Mint tropical palm fronds reaching in from the lower right corner">
      <defs>
        <linearGradient id="frondTone" x1="0" y1="0" x2="1" y2="1">
          <stop offset="0" stop-color="var(--leaf-light)" stop-opacity="0.5"/>
          <stop offset="1" stop-color="var(--leaf)"/>
        </linearGradient>
      </defs>
      <path d="M330 0 C250 40 120 120 0 290 L330 290 Z" fill="url(#frondTone)"/>
    </svg>
  </section>

  <section class="card card--back" aria-label="Business card back">
    <div class="brand">
      <span class="brand__dot" aria-hidden="true"></span>
      <div>
        <p class="brand__name">Cedar and Willow</p>
        <p class="brand__tagline">Massage Studio</p>
      </div>
    </div>
  </section>

</main>
</body>
</html>
```